Constant Contact email marketing template

I need engaging customizable templates that can be used in multiple fundraising campaigns.

I included a school bus project that we used in a previous campaign. This campaign, however, is a $25 for $25 promotion. Consumers make a $25 contribution for the school or charity and receive back a $25 e-gift card to be used at area restaurants.

Important! This is a completely generic piece, capable of being used in schools, churches, or other civic organizations.

The 5 part example is NOT what I am looking for. I included it to suggest the concept. I am looking forward to viewing YOUR designs,

Target Market(s)

schools, leagues, nonprofit organizations

Font styles to use
Sans Serif

Colors

Designer to choose colors to be used in the design.

Requirements
Must have
• Must clearly present itself as a fundraising tool for schools, leagues and Nonprofit organizations.
• Must have 2 clickable buttons that allow member to click

```html
<!DOCTYPE html>
<html lang="en">
<head>
<meta charset="utf-8">
<title>Donate $25, Get $25 – Fundraiser</title>
<link rel="stylesheet" href="https://fonts.googleapis.com/css2?family=Montserrat:wght@500;700;800&family=Oswald:wght@500;600&family=Kaushan+Script&family=Roboto+Condensed:wght@400&display=swap">
<style>
  :root{
    --ink:#111111;
    --night:#1a1a1a;
    --royal:#2c3a9c;
    --royal-soft:#3d52b5;
    --paper:#ffffff;
    --gold:#f7b924;
    --amber:#f0a830;
    --red:#e1251b;
    --crimson:#c4202b;
    --brand:#9b1c20;
    --silver:#d9dbe0;
  }
  *{margin:0;padding:0;box-sizing:border-box}
  html,body{width:1200px;height:2786px;overflow:hidden;background:var(--paper)}
  .flyer{position:relative;width:1200px;height:2786px;overflow:hidden;font-family:"Montserrat",Arial,sans-serif;color:var(--ink)}
  .backdrop{position:absolute;inset:0}
  .abs{position:absolute}

  .brand{left:410px;top:90px;width:382px;height:155px;background:var(--brand);display:flex;flex-direction:column;align-items:center;justify-content:center;color:var(--paper);font-weight:700;text-align:center}
  .brand-name{font-size:46px;letter-spacing:1px;line-height:1}
  .brand-sub{font-size:15px;letter-spacing:3px;margin-top:10px}

  .burst{left:63px;top:760px;width:530px;height:530px;display:flex;flex-direction:column;align-items:center;justify-content:center;text-align:center}
  .burst-greatest{font-family:"Kaushan Script",cursive;color:var(--paper);font-size:54px;line-height:1;margin-top:-10px}
  .burst-fundraiser{font-family:"Oswald",sans-serif;color:var(--amber);font-size:42px;letter-spacing:13px;margin:20px 0 0 13px;line-height:1}
  .burst-ever{font-family:"Kaushan Script",cursive;color:var(--paper);font-size:118px;line-height:1.1}

  .coin{display:flex;flex-direction:column;align-items:center;justify-content:center;text-align:center;width:318px;height:318px}
  .coin-donate{left:746px;top:1115px}
  .coin-card{left:836px;top:1413px}
  .coin-script{font-family:"Kaushan Script",cursive;color:var(--crimson);font-size:70px;line-height:1}
  .coin-label{font-family:"Oswald",sans-serif;color:var(--crimson);font-size:22px;letter-spacing:4px;margin-top:2px}
  .coin-amount{font-family:"Oswald",sans-serif;font-weight:600;color:var(--ink);font-size:118px;line-height:1.05}
  .coin-amount sup{font-size:62px;vertical-align:top;position:relative;top:24px}

  .and-you-get{font-family:"Kaushan Script",cursive;color:var(--royal-soft);font-size:104px;line-height:1;transform:rotate(-12deg);white-space:nowrap}
  .and-word{left:570px;top:1390px}
  .you-get-word{left:475px;top:1520px}

  .cta{display:flex;flex-direction:column;align-items:center;justify-content:center;width:318px;height:318px;border-radius:50%;text-decoration:none;text-align:center;font-family:"Oswald",sans-serif;line-height:1}
  .cta-main{left:54px;top:1722px;background:radial-gradient(circle at 40% 30%,#f1512f,var(--red) 55%,#b3160f)}
  .cta-plus{left:54px;top:2338px;background:radial-gradient(circle at 40% 30%,#ffd25a,var(--gold) 55%,#e39a12)}
  .cta-label{font-size:38px;letter-spacing:2px;margin-bottom:8px}
  .cta-main .cta-label{color:var(--gold)}
  .cta-plus .cta-label{color:var(--crimson)}
  .cta-row{display:flex;align-items:center;gap:8px;font-weight:500}
  .cta-main .cta-row{color:var(--paper)}
  .cta-plus .cta-row{color:var(--red)}
  .cta-num{font-size:100px}
  .cta-num sup{font-size:44px;vertical-align:top;position:relative;top:12px}
  .cta-for{font-size:24px;width:40px;text-align:right}
  .cta-main .cta-for{color:var(--gold)}
  .cta-plus .cta-for{color:var(--crimson)}
  .cta-spacer{width:40px}

  .headline{left:478px;top:1808px;font-size:46px;font-weight:800;line-height:56px;white-space:nowrap}

  .perks{left:150px;top:2094px;list-style:none;color:var(--red);font-weight:700;font-size:29px;white-space:nowrap}
  .perks li{display:flex;align-items:center;height:48px}
  .perks svg{width:30px;height:30px;margin-right:16px;flex:none}

  .upgrade-title{left:458px;top:2346px;font-size:62px;font-weight:700;color:var(--red);line-height:1;white-space:nowrap}
  .upgrade-text{left:462px;top:2440px;font-family:"Roboto Condensed",Arial,sans-serif;font-size:29px;line-height:40px;color:var(--ink);white-space:nowrap}

  .contact{right:40px;list-style:none;color:var(--paper);font-weight:700;font-size:27px;white-space:nowrap}
  .contact li{display:flex;align-items:center;justify-content:flex-end;height:58px}
  .contact svg{width:50px;height:50px;margin-left:18px;flex:none}
  .contact-list{top:2634px}
</style>
</head>
<body>
<main class="flyer">
  <svg class="backdrop" width="1200" height="2786" viewBox="0 0 603 1400" preserveAspectRatio="none" aria-hidden="true">
    <defs>
      <linearGradient id="nightFade" x1="0" y1="0" x2="1" y2="1">
        <stop offset="0" stop-color="#3a3a3a"/>
        <stop offset="1" stop-color="#0d0d0d"/>
      </linearGradient>
      <linearGradient id="burstFade" x1="0" y1="0" x2="1" y2="0">
        <stop offset="0" stop-color="#121212"/>
        <stop offset="1" stop-color="#8a8a8a"/>
      </linearGradient>
      <radialGradient id="silverRing" cx="0.4" cy="0.3" r="0.8">
        <stop offset="0" stop-color="#ffffff"/>
        <stop offset="1" stop-color="#b9bcc4"/>
      </radialGradient>
    </defs>
    <rect x="0" y="0" width="603" height="197" fill="var(--ink)"/>
    <path d="M0 197 H603 V880 C 420 700, 150 640, 0 610 Z" fill="var(--royal)"/>
    <path d="M0 197 H195 C 120 250, 50 320, 0 400 Z" fill="url(#nightFade)"/>
    <path d="M0 420 C 90 540, 230 600, 380 600 C 470 600, 545 560, 603 520 V 610 C 540 650, 460 672, 380 670 C 220 668, 90 610, 0 540 Z" fill="url(#nightFade)"/>
    <path d="M603 1140 C 590 1250, 420 1330, 280 1400 H603 Z" fill="var(--royal)"/>
    <circle cx="400" cy="305" r="226" fill="var(--paper)"/>
    <circle cx="165" cy="515" r="135" fill="var(--paper)"/>
    <circle cx="165" cy="515" r="127" fill="url(#burstFade)"/>
    <path d="M382 612 H349 V845 H420" fill="none" stroke="var(--gold)" stroke-width="2"/>
    <circle cx="455" cy="640" r="80" fill="var(--gold)"/>
    <circle cx="500" cy="789" r="80" fill="var(--gold)"/>
    <circle cx="107" cy="945" r="90" fill="url(#silverRing)"/>
    <circle cx="107" cy="1255" r="90" fill="url(#silverRing)"/>
  </svg>

  <div class="abs" role="img" aria-label="Photo of a cheering group of friends with raised arms" style="left:356px;top:165px;width:880px;height:880px;border-radius:50%;background:radial-gradient(circle at 45% 45%,#e7e2dc,#c9c1b8 55%,#f4f4f4 90%);clip-path:circle(48% at 50% 50%)"></div>

  <div class="abs brand">
    <span class="brand-name">RIDGEVIEW</span>
    <span class="brand-sub">SCHOOL DISTRICT</span>
  </div>

  <div class="abs burst">
    <span class="burst-greatest">greatest</span>
    <span class="burst-fundraiser">FUNDRAISER</span>
    <span class="burst-ever">ever!</span>
  </div>

  <div class="abs coin coin-donate">
    <span class="coin-script">donate</span>
    <span class="coin-amount"><sup>$</sup>25</span>
  </div>
  <div class="abs coin coin-card">
    <span class="coin-script">e-Gift</span>
    <span class="coin-label">CARD</span>
    <span class="coin-amount"><sup>$</sup>25</span>
  </div>

  <span class="abs and-you-get and-word">and</span>
  <span class="abs and-you-get you-get-word">you get</span>

  <a class="abs cta cta-main" href="#donate-25">
    <span class="cta-label">CLIK HERE</span>
    <span class="cta-row"><span class="cta-spacer"></span><span class="cta-num"><sup>$</sup>25</span></span>
    <span class="cta-row"><span class="cta-for">FOR</span><span class="cta-num"><sup>$</sup>25</span></span>
  </a>

  <p class="abs headline">Simply donate $25 and<br>we give you $25 back in<br>e-Gift Cards for<br>restaurants in your area!</p>

  <ul class="abs perks">
    <li><svg viewBox="0 0 30 30"><path d="M3 16 L11 25 L27 3" fill="none" stroke="var(--red)" stroke-width="5" stroke-linecap="round" stroke-linejoin="round"/></svg>More than 500,000 deals available every day</li>
    <li><svg viewBox="0 0 30 30"><path d="M3 16 L11 25 L27 3" fill="none" stroke="var(--red)" stroke-width="5" stroke-linecap="round" stroke-linejoin="round"/></svg>Local independent neughborhood restaurants</li>
    <li><svg viewBox="0 0 30 30"><path d="M3 16 L11 25 L27 3" fill="none" stroke="var(--red)" stroke-width="5" stroke-linecap="round" stroke-linejoin="round"/></svg>Always available. Never expire.</li>
    <li><svg viewBox="0 0 30 30"><path d="M3 16 L11 25 L27 3" fill="none" stroke="var(--red)" stroke-width="5" stroke-linecap="round" stroke-linejoin="round"/></svg>More than 62,000+ restaurants &amp; providers nationwide</li>
  </ul>

  <a class="abs cta cta-plus" href="#donate-30">
    <span class="cta-label">CLIK HERE</span>
    <span class="cta-row"><span class="cta-spacer"></span><span class="cta-num"><sup>$</sup>30</span></span>
    <span class="cta-row"><span class="cta-for">FOR</span><span class="cta-num"><sup>$</sup>50</span></span>
  </a>

  <h2 class="abs upgrade-title">$30 for $50</h2>
  <p class="abs upgrade-text">For only an extra $5 we will send<br>you an additional $25 e-Gift Card.</p>

  <ul class="abs contact contact-list">
    <li>www.tablegive.org
      <svg viewBox="0 0 50 50"><circle cx="25" cy="25" r="22" fill="none" stroke="var(--paper)" stroke-width="3"/><path d="M14 26 L25 15 L36 26 H32 V36 H18 V26 Z" fill="var(--paper)"/></svg>
    </li>
    <li>support@tablegive.org
      <svg viewBox="0 0 50 50"><circle cx="25" cy="25" r="22" fill="none" stroke="var(--paper)" stroke-width="3"/><rect x="14" y="17" width="22" height="16" rx="2" fill="var(--paper)"/><path d="M14 18 L25 27 L36 18" fill="none" stroke="var(--royal)" stroke-width="2"/></svg>
    </li>
  </ul>
</main>
</body>
</html>
```